Anzeigengestaltung für Verkauf & Installation von Alarmanlagen und Videoüberwachungssystemen
Zielgruppe
Verkauf und Installation von Alarmanlagen und Videoüberwachungssystemen.
Verkauf erfolgt über eigenen Onlineshop.
Installation der Anlagen im regionalen Umkreis, hauptsächlich Privatkunden.
Zielgruppe: Privatkunden, Familien, mit vorhandener Immobilie/Wohneigentum.
Aufgabenstellung
Zeitungsformat:
92 mm x 60 mm
s/w-4C
Text Entwurf als Orientierung befindet sich im Anhang, ebenso das Firmenlogo.
Bilder aus der Webseite sind ebenfalls beigefügt. Vielleicht lässt sich damit etwas anfangen, ich bin aber auch für Vorschläge aus geeigneten Stock-Bildern offen.

```html
<!DOCTYPE html>
<html lang="de">
<head>
<meta charset="utf-8">
<title>Wachturm Technik – Anzeige</title>
<link href="https://fonts.googleapis.com/css2?family=Oswald:wght@500&family=PT+Sans+Narrow:wght@700&family=Source+Sans+3:wght@600&display=swap" rel="stylesheet">
<style>
  :root {
    --red: #d8432f;
    --ink: #262626;
    --paper: #ececec;
    --paper-light: #f4f4f4;
    --page: #ffffff;
    --photo-dark: #59646b;
    --photo-light: #c9cdd0;
  }
  html, body {
    margin: 0;
    width: 1200px;
    height: 2400px;
    overflow: hidden;
    background: var(--page);
  }
  .ad {
    position: absolute;
    left: 50px;
    top: 842px;
    width: 1100px;
    height: 716px;
    overflow: hidden;
    background: linear-gradient(135deg, var(--paper-light), var(--paper) 60%, #e4e4e4);
    font-family: "Source Sans 3", sans-serif;
    color: var(--ink);
  }
  .ad-visual { position: absolute; left: 0; top: 0; }
  .brand {
    position: absolute;
    left: 560px;
    top: 70px;
    display: flex;
    align-items: center;
    gap: 24px;
  }
  .brand-mark {
    width: 100px;
    height: 100px;
    border-radius: 50%;
    background: var(--ink);
  }
  .brand-name {
    font-family: "Oswald", sans-serif;
    font-weight: 500;
    font-size: 48px;
    line-height: 1;
    color: var(--ink);
  }
  .headline {
    position: absolute;
    left: 601px;
    top: 236px;
    margin: 0;
    font-family: "Oswald", sans-serif;
    font-weight: 500;
    font-size: 37px;
    letter-spacing: -0.3px;
    color: var(--ink);
  }
  .benefits {
    position: absolute;
    left: 601px;
    top: 296px;
    margin: 0;
    padding: 0;
    list-style: none;
  }
  .benefits li {
    display: flex;
    align-items: center;
    gap: 14px;
    height: 42px;
    font-family: "Oswald", sans-serif;
    font-weight: 500;
    font-size: 29px;
    color: var(--red);
  }
  .benefits svg { width: 30px; height: 30px; flex: none; }
  .funding-band {
    position: absolute;
    left: 582px;
    top: 460px;
    width: 540px;
    height: 68px;
    border-radius: 34px 0 0 34px;
    background: var(--red);
    color: #fff;
    font-family: "Oswald", sans-serif;
    font-weight: 500;
    font-size: 35px;
    line-height: 68px;
    padding-left: 52px;
    box-sizing: border-box;
  }
  .services {
    position: absolute;
    left: 601px;
    top: 555px;
    display: flex;
    gap: 30px;
    font-family: "PT Sans Narrow", sans-serif;
    font-weight: 700;
    font-size: 25px;
  }
  .service { display: flex; align-items: center; gap: 10px; }
  .service svg { height: 40px; }
  .contact {
    position: absolute;
    right: 28px;
    top: 620px;
    text-align: right;
    font-size: 22px;
    line-height: 32px;
  }
  .contact .dot { color: var(--red); padding: 0 4px; }
</style>
</head>
<body>
<section class="ad" aria-label="Anzeige Wachturm Technik">
  <svg class="ad-visual" width="1100" height="716" viewBox="0 0 1100 716">
    <defs>
      <linearGradient id="photoTone" x1="0" y1="0" x2="1" y2="1">
        <stop offset="0" stop-color="var(--photo-light)"/>
        <stop offset="0.55" stop-color="#8f999f"/>
        <stop offset="1" stop-color="var(--photo-dark)"/>
      </linearGradient>
    </defs>
    <polygon role="img" aria-label="Foto: behandschuhte Hand greift durch eine spaltbreit geöffnete Tür nach der Türkette"
             points="0,0 439,0 567,354 366,716 0,716" fill="url(#photoTone)"/>
    <polyline points="439,0 567,354 366,716" fill="none" stroke="var(--red)" stroke-width="5"/>
  </svg>

  <div class="brand">
    <div class="brand-mark"></div>
    <div class="brand-name">Wachturm Technik</div>
  </div>

  <h1 class="headline">MODERNE FUNKALARMANLAGEN</h1>

  <ul class="benefits">
    <li><svg viewBox="0 0 30 30"><rect x="2" y="6" width="22" height="22" fill="none" stroke="#d8432f" stroke-width="3"/><path d="M7 16 l6 6 L28 3" fill="none" stroke="#d8432f" stroke-width="4"/></svg>Individuelle Beratung</li>
    <li><svg viewBox="0 0 30 30"><rect x="2" y="6" width="22" height="22" fill="none" stroke="#d8432f" stroke-width="3"/><path d="M7 16 l6 6 L28 3" fill="none" stroke="#d8432f" stroke-width="4"/></svg>Onlineshop</li>
    <li><svg viewBox="0 0 30 30"><rect x="2" y="6" width="22" height="22" fill="none" stroke="#d8432f" stroke-width="3"/><path d="M7 16 l6 6 L28 3" fill="none" stroke="#d8432f" stroke-width="4"/></svg>Installation</li>
  </ul>

  <div class="funding-band">LBF FÖRDERUNG MÖGLICH</div>

  <div class="services">
    <div class="service">
      <svg viewBox="0 0 56 40" width="56"><path d="M6 8 q-6 12 0 24 M12 12 q-4 8 0 16 M50 8 q6 12 0 24 M44 12 q4 8 0 16" fill="none" stroke="#262626" stroke-width="2.5"/><circle cx="28" cy="20" r="15" fill="#d8432f"/><rect x="21" y="12" width="14" height="16" rx="2" fill="#fff"/><rect x="23" y="14" width="10" height="3" fill="#d8432f"/></svg>Alarm
    </div>
    <div class="service">
      <svg viewBox="0 0 40 40" width="40"><path d="M3 12 V3 H12 M28 3 H37 V12 M37 28 V37 H28 M12 37 H3 V28" fill="none" stroke="#262626" stroke-width="3"/><circle cx="20" cy="20" r="6" fill="#d8432f"/></svg>Video
    </div>
    <div class="service">
      <svg viewBox="0 0 46 40" width="46"><path d="M2 20 L16 8 L30 20" fill="none" stroke="#262626" stroke-width="3"/><rect x="7" y="19" width="18" height="16" fill="none" stroke="#262626" stroke-width="3"/><rect x="28" y="10" width="15" height="27" rx="2" fill="#262626"/><path d="M35.5 16 l4 7 h-8 z" fill="#d8432f"/></svg>Hausautomation
    </div>
  </div>

  <address class="contact" style="font-style:normal">
    <div>Lindenstraße 12<span class="dot">•</span>71234 Musterfeld<span class="dot">•</span>07100-4321</div>
    <div>www.wachturm-technik.de&nbsp; E-Mail: info@wachturm-technik.de</div>
  </address>
</section>
</body>
</html>
```